Fern Acupuncture Business Card Design

I would like a business card design for my acupuncture business which is based from 2 practices in Melbourne, Australia.

The front of the card should include:

*The Logo
* Name - Miranda Tesselhoff (B.App.Sc.(TCM), Dip.Rem.Mass.). (I would like the letters after my name in slightly smaller font)
* Mobile number - 0472 318 604
* Web address - www.fernacupuncture.com.au

On the back of the card I would somehow like to fit my 2 clinic addresses in. They are:

The Calm & Balance Rooms
842 Pellam St, Camberwell VIC 3124
Ph: 1300 287 419

Riverbend Natural Therapies & Herbal Practice
19 Quillon Ave, Malvern East VIC 3145
Ph: (03) 9731 4052

If there is space, I'd also like to add to the back of the card - Next Appointment............................ (or something along those lines).

Thanks and happy designing!

Target Market(s)

Health consumers, and colleagues in the health industry

Industry/Entity Type

Clinic

Contact Information for Business Card

as above in brief

Requirements
Must have
• I've seen some ok designs coming in, however I'd like to avoid the generic look with the added curved line details etc. I don't particularly need extra patterns added to the card. I'd prefer it to look quite clean and simple, and using more earthy colours (I'm not super keen on the lime green that a lot of designs seem to include. I don't mind the full black or white look, (obviously the back side needs to be a lighter colour to allow me to write appointment details on it). I also quite like the idea of the background looking like brown recycled paper (just an idea - that's not 100% necessary).
Nice to have
• I have an idea that I could have the main flower part of the logo printed as metallic.
Should not have
• Generic patterns and too much added detail.

```html
<!DOCTYPE html>
<html lang="en">
<head>
<meta charset="utf-8">
<title>Fern Acupuncture – Business Card</title>
<link href="https://fonts.googleapis.com/css2?family=Open+Sans:wght@400;600;700&display=swap" rel="stylesheet">
<style>
  :root {
    --backdrop: #e9e3da;
    --card: #fffdf9;
    --ink: #2b2520;
    --ink-soft: #4a423a;
    --sage: #7d8a55;
    --sage-dark: #5f6b3c;
    --clay: #8a6747;
    --clay-dark: #6b4e35;
    --stone: #a89378;
    --gold: #b8975a;
    --gold-light: #e8dcbc;
    --rule: #6b5f54;
    --on-band: #fbf7ef;
  }
  * { box-sizing: border-box; margin: 0; padding: 0; }
  html, body { width: 1200px; height: 913px; overflow: hidden; }
  body {
    background: var(--backdrop);
    font-family: "Open Sans", Arial, sans-serif;
    color: var(--ink);
    position: relative;
  }
  .card {
    position: absolute;
    width: 540px;
    height: 330px;
    background: var(--card);
    box-shadow: 0 6px 18px rgba(60,40,20,0.18);
    overflow: hidden;
  }
  .card-front { left: 40px; top: 150px; }
  .card-back { left: 620px; top: 433px; }

  /* Front */
  .brand {
    position: absolute;
    right: 40px;
    top: 42px;
    display: flex;
    align-items: center;
    gap: 12px;
  }
  .brand-mark {
    width: 22px; height: 22px;
    border-radius: 50%;
    background: var(--gold);
  }
  .brand-name {
    font-weight: 700;
    font-size: 24px;
    color: var(--ink);
    letter-spacing: 0.5px;
  }
  .holder {
    position: absolute;
    left: 30px;
    top: 150px;
  }
  .holder-name { font-size: 21px; font-weight: 700; color: var(--ink); }
  .holder-quals { font-size: 12px; color: var(--ink-soft); margin-top: 2px; }

  .bands { position: absolute; left: 0; bottom: 0; width: 540px; height: 130px; }
  .web {
    position: absolute;
    right: 24px;
    top: 214px;
    font-size: 14px;
    color: var(--on-band);
  }
  .contact {
    position: absolute;
    left: 24px;
    bottom: 22px;
    font-size: 14px;
    color: var(--on-band);
    list-style: none;
  }
  .contact li { display: flex; align-items: center; gap: 10px; margin-top: 8px; }
  .contact svg { width: 14px; height: 14px; }

  /* Back */
  .edge-top {
    position: absolute; left: 0; top: 0; width: 100%; height: 12px;
    background: linear-gradient(90deg, var(--gold) 0%, var(--gold-light) 40%, var(--stone) 75%, var(--clay) 100%);
  }
  .edge-bottom {
    position: absolute; left: 0; bottom: 0; width: 100%; height: 14px;
    background: linear-gradient(90deg, var(--clay) 0%, var(--stone) 30%, var(--gold-light) 65%, var(--gold) 100%);
  }
  .section-title {
    position: absolute; left: 30px; top: 30px;
    font-size: 13px; font-weight: 700; color: var(--clay);
    letter-spacing: 0.5px;
  }
  .clinic {
    position: absolute; top: 56px;
    font-size: 12.5px; line-height: 1.45; color: var(--ink);
    font-style: normal;
  }
  .clinic-one { left: 30px; width: 235px; }
  .clinic-two { left: 280px; width: 240px; }
  .clinic-name { font-weight: 700; }
  .appointment { position: absolute; left: 30px; right: 30px; top: 168px; font-size: 13px; }
  .appt-line { display: flex; align-items: flex-end; height: 34px; }
  .appt-label { font-weight: 600; margin-right: 6px; white-space: nowrap; }
  .appt-dots { flex: 1; border-bottom: 2px dotted var(--rule); margin-bottom: 4px; }
</style>
</head>
<body>

<section class="card card-front" aria-label="Card front">
  <div class="brand">
    <span class="brand-mark"></span>
    <span class="brand-name">Fern Acupuncture</span>
  </div>

  <div class="holder">
    <p class="holder-name">Miranda Tesselhoff</p>
    <p class="holder-quals">B.App.Sc.(TCM), Dip.Rem.Mass.</p>
  </div>

  <svg class="bands" viewBox="0 0 540 130" aria-hidden="true">
    <defs>
      <linearGradient id="clayBand" x1="0" y1="0" x2="0" y2="1">
        <stop offset="0" stop-color="#8a6747"/>
        <stop offset="1" stop-color="#6b4e35"/>
      </linearGradient>
      <linearGradient id="sageBand" x1="0" y1="0" x2="0" y2="1">
        <stop offset="0" stop-color="#7d8a55"/>
        <stop offset="1" stop-color="#5f6b3c"/>
      </linearGradient>
    </defs>
    <rect x="0" y="0" width="540" height="130" fill="url(#clayBand)"/>
    <polygon points="0,38 290,38 340,130 0,130" fill="url(#sageBand)"/>
    <polygon points="0,0 270,0 290,38 0,38" fill="#fffdf9"/>
  </svg>

  <p class="web">www.fernacupuncture.com.au</p>

  <ul class="contact">
    <li>
      <svg viewBox="0 0 24 24" aria-hidden="true"><path fill="#fbf7ef" d="M6.6 10.8a15.1 15.1 0 0 0 6.6 6.6l2.2-2.2a1 1 0 0 1 1-.25 11.4 11.4 0 0 0 3.6.57 1 1 0 0 1 1 1V20a1 1 0 0 1-1 1A17 17 0 0 1 3 4a1 1 0 0 1 1-1h3.5a1 1 0 0 1 1 1c0 1.25.2 2.45.57 3.6a1 1 0 0 1-.25 1z"/></svg>
      <span>0472 318 604</span>
    </li>
    <li>
      <svg viewBox="0 0 24 24" aria-hidden="true"><path d="M2 5h20v14H2z M3 6l9 7 9-7" fill="none" stroke="#fbf7ef" stroke-width="2"/></svg>
      <span>miranda@fernacupuncture.com.au</span>
    </li>
  </ul>
</section>

<section class="card card-back" aria-label="Card back">
  <div class="edge-top"></div>

  <h2 class="section-title">CLINIC ADDRESSES</h2>

  <address class="clinic clinic-one">
    <p class="clinic-name">The Calm &amp; Balance Rooms</p>
    <p>842 Pellam St, Camberwell VIC 3124</p>
    <p>Ph: 1300 287 419</p>
  </address>

  <address class="clinic clinic-two">
    <p class="clinic-name">Riverbend Natural Therapies &amp;<br>Herbal Practice</p>
    <p>19 Quillon Ave, Malvern East</p>
    <p>VIC 3145 • Ph: (03) 9731 4052</p>
  </address>

  <div class="appointment">
    <div class="appt-line"><span class="appt-label">Next Appointment</span><span class="appt-dots"></span></div>
    <div class="appt-line"><span class="appt-dots"></span></div>
    <div class="appt-line"><span class="appt-dots"></span></div>
  </div>

  <div class="edge-bottom"></div>
</section>

</body>
</html>
```